House flipping business web site needed

pinecrestholdingsgroup.example.
I am a residential developer in Northern NJ and I am looking for a fresh new updated website. I have an intro video about my company being made now. I don't update it very often but I want an easy format that I can add update photos to on projects I have worked on or homes I renovate for sale.

Target Market(s)

investors into my projects so a portfolio , people looking to sell their homes to me.

Industry/Entity Type

Real Estate Development

Number of Pages Required

4 page

Font styles to use
Serif

Colors
33b8a4
39a9d7
cadf82

Requirements
Must have
• space for an intro video about my company
• a portfolio with pictures and information about each project
• Markets we serve- Morris County, NJ
• My logo- already created
• SEO
• Yes I would like this to function over all platforms. Phone, computer, all platforms.
• history and background page
• I am looking for a completed page that I can upload to the site that hosts my website
Nice to have
• I want something creative, easy to navigate. modern.

```html
<!DOCTYPE html>
<html lang="en">
<head>
<meta charset="utf-8">
<title>Pinecrest Holdings Group</title>
<link href="https://fonts.googleapis.com/css2?family=Lato:wght@400;900&family=Raleway:wght@400;500&family=Open+Sans:wght@400;600&display=swap" rel="stylesheet">
<style>
:root{
  --teal:#33b8a4;
  --sky:#27a8e8;
  --lime:#8cc63f;
  --navy:#2f5b8c;
  --navy-dark:#3b5e8e;
  --ink:#222;
  --text:#555;
  --muted:#888;
  --line:#e3e8ee;
  --white:#fff;
}
*{box-sizing:border-box;margin:0;padding:0}
html,body{width:1200px;height:2187px;overflow:hidden;background:var(--white)}
body{position:relative;font-family:"Open Sans",Arial,sans-serif;color:var(--text)}
.abs{position:absolute}

/* header */
.site-header{position:absolute;left:0;top:0;width:1200px;height:156px}
.brand{position:absolute;left:71px;top:20px;display:flex;align-items:center;gap:14px;height:110px}
.brand-mark{width:34px;height:34px;background:var(--teal)}
.brand-name{font-family:"Raleway",sans-serif;font-weight:500;font-size:26px;color:var(--navy);line-height:1.15;width:190px}
.call{position:absolute;right:80px;top:48px;text-align:right}
.call-label{font-family:"Raleway",sans-serif;font-size:19px;color:var(--navy)}
.call-number{display:flex;align-items:center;gap:12px;margin-top:10px;font-family:"Raleway",sans-serif;font-size:27px;color:var(--sky)}

/* nav */
.main-nav{position:absolute;left:0;top:156px;width:1200px;height:52px;background:var(--sky);display:flex;padding-left:120px}
.main-nav a{display:block;height:52px;line-height:52px;width:228px;text-align:center;color:var(--white);text-decoration:none;font-family:"Raleway",sans-serif;font-size:19px;text-transform:uppercase}
.main-nav a.active{background:var(--lime);color:var(--ink)}
.main-nav a:nth-child(3){width:250px}

/* hero */
.hero{position:absolute;left:0;top:208px;width:1200px;height:542px;background:linear-gradient(180deg,#b9cde6 0%,#e4e9ef 38%,#c8a985 58%,#5c7f94 78%,#8b7a63 100%)}
.hero h1{position:absolute;left:0;top:166px;width:1200px;text-align:center;font-family:"Lato",sans-serif;font-weight:900;font-size:49px;line-height:57px;color:#000;text-transform:uppercase;letter-spacing:-0.5px}

/* features */
.features{position:absolute;left:77px;top:668px;width:1046px;height:197px;background:linear-gradient(180deg,#fff 75%,#eef5fc 100%);box-shadow:0 18px 40px rgba(0,0,0,.10);display:flex}
.feature{flex:1;display:flex;gap:10px;padding:42px 0 0 30px;border-right:1px solid var(--line)}
.feature:last-child{border-right:none}
.feature h3{font-family:"Raleway",sans-serif;font-weight:400;font-size:25px;color:var(--navy);margin-bottom:8px}
.feature p{font-size:14px;line-height:23px;color:var(--muted);width:215px}
.feature .more{display:block;margin-top:10px;font-size:18px;color:var(--ink);text-decoration:none}

/* welcome */
.welcome-title{position:absolute;left:0;top:910px;width:1200px;text-align:center;font-family:"Raleway",sans-serif;font-weight:400;font-size:46px;color:var(--navy)}
.accent{color:var(--teal)}
.welcome-copy{position:absolute;left:80px;top:978px;width:640px;font-size:15px;line-height:25px;color:var(--text)}
.welcome-copy p+p{margin-top:25px}
.video{position:absolute;left:733px;top:981px;width:390px;height:197px;background:linear-gradient(135deg,#3e4c5c 0%,#2e3d4f 45%,#8a5040 70%,#2a3646 100%);display:flex;align-items:center;justify-content:center}
.btn{position:absolute;display:inline-block;background:var(--navy-dark);color:var(--white);text-decoration:none;border-radius:3px;font-family:"Open Sans",sans-serif}
.btn-read{left:77px;top:1207px;width:156px;height:47px;line-height:47px;text-align:center;font-size:19px}
.divider{position:absolute;left:200px;width:800px;height:2px;background:linear-gradient(90deg,transparent,#dde3ea,transparent)}

/* portfolio */
.portfolio-title{position:absolute;left:0;top:1343px;width:1200px;text-align:center;font-family:"Raleway",sans-serif;font-size:46px;color:var(--navy)}
.filters{position:absolute;left:0;top:1410px;width:1200px;display:flex;justify-content:center;gap:26px;font-family:"Raleway",sans-serif;font-size:21px;color:var(--text)}
.filters .current{border-bottom:2px solid var(--teal);padding:0 8px 4px}
.project{position:absolute;top:1465px;width:293px}
.project-photo{height:150px}
.project h4{margin-top:18px;font-family:"Raleway",sans-serif;font-weight:400;font-size:23px;color:#555}
.project h4.hl{color:var(--sky)}
.project p{margin-top:12px;font-size:14px;line-height:23px;color:var(--muted)}
.project .more{display:block;margin-top:10px;font-family:"Raleway",sans-serif;font-size:20px;color:#555;text-decoration:none}
.project .more.hl{color:var(--sky);text-decoration:underline}

/* footer */
.foot-col{position:absolute;top:1840px}
.foot-col h5{font-family:"Raleway",sans-serif;font-weight:400;font-size:19px;color:var(--ink);margin-bottom:18px}
.contact-line{display:flex;gap:8px;font-size:13px;line-height:23px;color:#666;margin-bottom:8px}
.socials{display:flex;gap:14px;margin-top:40px}
.socials span{width:52px;height:52px;border-radius:50%;border:2px solid var(--navy-dark)}
.socials span:first-child{background:var(--navy-dark)}
.news-lead{font-size:13px;line-height:22px;color:#888;width:290px}
.email-field{margin-top:18px;width:293px;height:46px;border:1px solid #ccd;border-radius:3px;padding-left:12px;line-height:44px;font-size:13px;color:#bbb}
.btn-sub{position:static;margin-top:18px;background:var(--teal);width:136px;height:46px;line-height:46px;text-align:center;font-size:18px}
.news-item{display:flex;gap:14px;margin-bottom:22px}
.news-thumb{width:62px;height:62px;flex:none}
.news-item h6{font-size:15px;font-weight:600;color:#444}
.news-item time{display:block;font-size:13px;color:#bbb;line-height:22px}
.news-item p{font-size:13px;line-height:20px;color:#777;width:210px}
.copyright{position:absolute;left:0;top:2134px;width:1200px;height:53px;background:var(--navy-dark);color:var(--white);text-align:center;line-height:53px;font-size:15px}
.copyright b{color:#000;font-weight:600}
</style>
</head>
<body>

<header class="site-header">
  <div class="brand"><span class="brand-mark"></span><span class="brand-name">Pinecrest Holdings Group</span></div>
  <div class="call">
    <div class="call-label">Call Us on</div>
    <div class="call-number">
      <svg width="42" height="42" viewBox="0 0 42 42"><circle cx="21" cy="21" r="19" fill="none" stroke="#27a8e8" stroke-width="2"/><path d="M15 13c1-1 2-1 3 0l2 3c.5 1 0 2-1 2.5 1 2 2.5 3.5 4.5 4.5.5-1 1.5-1.5 2.5-1l3 2c1 1 1 2 0 3l-1.5 1.5c-5 0-12-7-12-12z" fill="#27a8e8"/></svg>
      555-014-7878
    </div>
  </div>
</header>

<nav class="main-nav">
  <a href="#" class="active">Home</a><a href="#">About</a><a href="#">Portfolio</a><a href="#">Contact</a>
</nav>

<section class="hero" role="img" aria-label="Photo of a Mediterranean-style stone home with a pool and lounge chairs under a blue sky">
  <h1>We bring excellence to the<br>home buying and renovation<br>business.</h1>
</section>

<section class="features">
  <div class="feature">
    <svg width="50" height="56" viewBox="0 0 50 56"><circle cx="25" cy="25" r="22" fill="none" stroke="#33b8a4" stroke-width="4"/><path d="M17 20a8 8 0 1 1 12 7c-3 2-4 3-4 6" fill="none" stroke="#33b8a4" stroke-width="5"/><circle cx="25" cy="40" r="3" fill="#33b8a4"/><path d="M30 46l8 8 2-10z" fill="#33b8a4"/></svg>
    <div><h3>How we can help</h3><p>Do you need to sell your home fast to avoid foreclosure...</p><a class="more" href="#">READ MORE &raquo;</a></div>
  </div>
  <div class="feature">
    <svg width="56" height="56" viewBox="0 0 56 56"><circle cx="28" cy="28" r="27" fill="#33b8a4"/><text x="28" y="39" text-anchor="middle" font-family="Lato,sans-serif" font-weight="900" font-size="32" fill="#fff">$</text></svg>
    <div><h3>Financing</h3><p>We can close quickly and we buy with Cash...</p><a class="more" href="#">READ MORE &raquo;</a></div>
  </div>
  <div class="feature">
    <svg width="66" height="66" viewBox="0 0 66 66"><circle cx="33" cy="33" r="30" fill="none" stroke="#33b8a4" stroke-width="4"/><path d="M12 52L54 14" stroke="#33b8a4" stroke-width="4"/><path d="M18 36l10-9 10 9v12H18z" fill="#33b8a4"/><path d="M34 26l8-7 8 7v10H34z" fill="#33b8a4"/></svg>
    <div><h3>Your Neighborhood</h3><p>We only buy and renovate homes in our neighborhoods...</p><a class="more" href="#">READ MORE &raquo;</a></div>
  </div>
</section>

<h2 class="welcome-title">Welcome To <span class="accent">PINECREST Holdings</span></h2>
<div class="welcome-copy">
  <p>Pinecrest Holdings Group is a family run business with 3rd generation builders and renovators in the Morris County area. As the President and owner of Pinecrest Holdings Group I am dedicated to working hard to create opportunities for investment through real estate.</p>
  <p>At Pinecrest Holdings Group we have a valuable support system and a team of investors, realtors, attorneys, contractors and property managers providing a combined package offering years of experience in the local market.</p>
</div>
<div class="video" role="img" aria-label="Intro video still of the owner outdoors by a lake in autumn">
  <svg width="54" height="54" viewBox="0 0 54 54"><circle cx="27" cy="27" r="26" fill="#fff"/><path d="M21 15l18 12-18 12z" fill="#111"/></svg>
</div>
<a class="btn btn-read" href="#">READ MORE</a>

<div class="divider" style="top:1295px"></div>

<h2 class="portfolio-title">Our <span class="accent">Portfolio</span></h2>
<div class="filters"><span class="current">All</span><span>/</span><span>Rockaway</span><span>/</span><span>Denville</span><span>/</span><span>Boonton</span></div>

<article class="project" style="left:77px">
  <div class="project-photo" role="img" aria-label="Photo of a house under renovation in snowy woods" style="background:linear-gradient(160deg,#d9d6d0,#6d5a48 55%,#3a2e25)"></div>
  <h4 class="hl">Lorem Ipsum is simply text</h4>
  <p>Lorem Ipsum is simply dummy text of the printing and typesetting industry.</p>
  <a class="more hl" href="#">READ MORE</a>
</article>
<article class="project" style="left:453px">
  <div class="project-photo" role="img" aria-label="Photo of a two-storey green house under a blue sky" style="background:linear-gradient(180deg,#6fa6d8,#3d5a4f 55%,#4e5c54)"></div>
  <h4>Lorem Ipsum is simply text</h4>
  <p>Lorem Ipsum is simply dummy text of the printing and typesetting industry.</p>
  <a class="more" href="#">READ MORE &raquo;</a>
</article>
<article class="project" style="left:830px">
  <div class="project-photo" role="img" aria-label="Photo of a small grey cottage before renovation" style="background:linear-gradient(180deg,#5b6b3f,#9aa1ad 45%,#7a7c78)"></div>
  <h4>Lorem Ipsum is simply text</h4>
  <p>Lorem Ipsum is simply dummy text of the printing and typesetting industry.</p>
  <a class="more" href="#">READ MORE &raquo;</a>
</article>

<div class="divider" style="top:1796px"></div>

<div class="foot-col" style="left:80px">
  <h5>Contact US</h5>
  <div class="contact-line"><svg width="16" height="22" viewBox="0 0 16 22"><path d="M8 0a8 8 0 0 1 8 8c0 6-8 14-8 14S0 14 0 8a8 8 0 0 1 8-8z" fill="#888"/><circle cx="8" cy="8" r="3" fill="#fff"/></svg><span>Pinecrest Holdings Group | Morris County,<br>NJ | 555-231-PINE (7463)</span></div>
  <div class="contact-line"><svg width="20" height="20" viewBox="0 0 20 20"><path d="M4 1c1-1 2-1 3 0l2 3c.5 1 0 2-1 2.5 1 2.5 3 4.5 5.5 5.5.5-1 1.5-1.5 2.5-1l3 2c1 1 1 2 0 3l-2 2C10 18 2 10 2 3z" fill="#888"/></svg><span>+(555) 014 1212</span></div>
  <div class="contact-line"><svg width="20" height="16" viewBox="0 0 20 16"><rect width="20" height="16" rx="2" fill="#888"/><path d="M1 2l9 7 9-7" fill="none" stroke="#fff" stroke-width="1.5"/></svg><span>info@pinecrestholdingsgroup.example</span></div>
  <div class="socials" aria-label="Social links"><span></span><span></span><span></span></div>
</div>

<div class="foot-col" style="left:442px">
  <h5>Newsletter</h5>
  <p class="news-lead">Lorem Ipsum is simply dummy text<br>of the printing and typesetting.</p>
  <div class="email-field">E mail Id</div>
  <a class="btn btn-sub" href="#">SUBSCRIBE</a>
</div>

<div class="foot-col" style="left:830px">
  <h5>Recent News</h5>
  <div class="news-item">
    <div class="news-thumb" role="img" aria-label="Photo of a renovated kitchen" style="background:linear-gradient(135deg,#7a3a22,#c77a44)"></div>
    <div><h6>Lorem Ipsum is simply</h6><time>8th Sep,2016</time><p>Lorem Ipsum has been the industry's standard dummy text</p></div>
  </div>
  <div class="news-item">
    <div class="news-thumb" role="img" aria-label="Photo of a house exterior" style="background:linear-gradient(135deg,#c9c3b8,#5a4b3c)"></div>
    <div><h6>Lorem Ipsum is simply</h6><time>8th Sep,2016</time><p>Lorem Ipsum has been the industry's standard dummy text</p></div>
  </div>
</div>

<footer class="copyright">Copyright 2016 ~ <b>Pinecrest Holdings Group</b> ~All rights reserved.</footer>

</body>
</html>
```